qoBureau Business Card Design Project

We need a business card design for qoBureau. qoBureau is an underwriting agency. Underwriting agencies act on behalf of insurers, to underwrite insurance. We will be operating in specialised classes of insurance initially and looking to expand from there. We would like to see designs that incorporate our logo colours as well as a contrasting stand out colour - also we'd like the logo itself to be embossed on the card.

Industry/Entity Type

Insurance

Requirements
Must have
• Logo on front
Nice to have
• Logo solely featured on back of card
Should not have
• Please do not use comic cans font :)

```html
<!DOCTYPE html>
<html lang="en">
<head>
<meta charset="utf-8">
<title>qoBureau Business Card</title>
<link rel="stylesheet" href="https://fonts.googleapis.com/css2?family=Arimo:wght@400;700&family=Tinos:wght@400;700&display=swap">
<style>
  :root {
    --backdrop-light: #f2f2f2;
    --backdrop-dark: #b9b9b9;
    --card-blue: #3d7fd8;
    --card-blue-deep: #2c68c2;
    --band-blue: #1d5cc4;
    --band-edge: #4f92e6;
    --ink-white: #ffffff;
    --ink-soft: #e6efff;
    --wordmark-silver: #e3e9f1;
  }
  * { margin: 0; padding: 0; box-sizing: border-box; }
  html, body {
    width: 1200px;
    height: 801px;
    overflow: hidden;
  }
  body {
    background: radial-gradient(ellipse at 45% 35%, var(--backdrop-light) 0%, #dcdcdc 55%, var(--backdrop-dark) 100%);
    position: relative;
  }
  .card {
    position: absolute;
    top: 258px;
    width: 500px;
    height: 286px;
    border-radius: 4px;
    overflow: hidden;
    background: linear-gradient(160deg, var(--card-blue) 0%, var(--card-blue-deep) 100%);
    box-shadow: 0 14px 30px rgba(0, 0, 0, 0.28);
  }
  .card--details { left: 70px; }
  .card--brand { left: 630px; }

  /* details side */
  .contact {
    position: absolute;
    inset: 0;
    display: flex;
    flex-direction: column;
    align-items: center;
    justify-content: center;
    text-align: center;
    color: var(--ink-white);
    font-family: "Tinos", "Times New Roman", serif;
  }
  .contact__name {
    font-size: 34px;
    font-weight: 700;
    letter-spacing: 0.5px;
    line-height: 1;
  }
  .contact__title {
    font-size: 13px;
    color: var(--ink-soft);
    margin: 4px 0 12px;
  }
  .contact__line {
    font-size: 17px;
    line-height: 1.2;
  }

  /* brand side */
  .brand-band {
    position: absolute;
    left: 0;
    right: 0;
    bottom: 0;
    height: 38px;
    background: linear-gradient(180deg, var(--band-edge) 0%, var(--band-blue) 30%, var(--band-blue) 100%);
  }
  .brand-name {
    position: absolute;
    left: 0;
    right: 0;
    top: 0;
    bottom: 38px;
    display: flex;
    align-items: center;
    justify-content: center;
    font-family: "Arimo", Arial, sans-serif;
    font-weight: 700;
    font-size: 64px;
    line-height: 1;
    letter-spacing: -1px;
    color: var(--wordmark-silver);
  }
</style>
</head>
<body>
  <section class="card card--details" aria-label="Business card, contact side">
    <div class="contact">
      <p class="contact__name">Your Name</p>
      <p class="contact__title">Job Title</p>
      <p class="contact__line">Company Name</p>
      <p class="contact__line">yourname@yourcompany.com</p>
      <p class="contact__line">232 address Lane</p>
      <p class="contact__line">Mobile Number</p>
      <p class="contact__line">Website Address</p>
    </div>
  </section>

  <section class="card card--brand" aria-label="Business card, brand side">
    <p class="brand-name">qoBureau</p>
    <div class="brand-band"></div>
  </section>
</body>
</html>
```